Business card design for holistic health care clinic

We need a double-sided business card design for our holistic health care clinic that integrates our logo design and also its color scheme. My business is called Valmira. It is an integrative medicine clinic. You have already done the logo for me. Please ensure an elegant and upscale design that is not cluttered, but still has all the necessary information (please see below for details).

Target Market(s)

Wellness, fitness, rehabilitation for educated, well-traveled open-minded clients who are focused on natural, organic, balanced and preventive healthcare and lifestyle.

Industry/Entity Type

Medical

Contact Information for Business Card

Modern, clean.

Number of Pages Required

1 page

Font styles to use
Serif
Sans Serif

Colors

Designer to choose colors to be used in the design.

Requirements
Must have
• Logo on one side, all other information on the other side.
• Other information should include:
• Tobias Wrenfeld - DOE, CPT, LMT
• 4100 East Marrow Drive
• Austin, TX 78119
• 512 555 0148
• 818 555 0192
• info@ValmiraHealth.example
• t.wrenfeld@ValmiraHealth.example
Nice to have
• Darker background on front - but not totally black - shaded/dark gray.

```html
<!DOCTYPE html>
<html lang="en">
<head>
<meta charset="utf-8">
<title>Valmira – Business Card</title>
<link href="https://fonts.googleapis.com/css2?family=Nunito:wght@400;700&family=Roboto:wght@400;700&display=swap" rel="stylesheet">
<style>
  :root{
    --stage:#d9d6d2;
    --card-dark:#0b0c0e;
    --card-dark-edge:#2a2c30;
    --card-frost:#ecebe8;
    --card-frost-deep:#d8d7d4;
    --brand-blue:#1f78c1;
    --brand-blue-deep:#0f4f8c;
    --ink:#1c1c1e;
  }
  *{margin:0;padding:0;box-sizing:border-box}
  html,body{width:1200px;height:969px;overflow:hidden;background:var(--stage)}
  .card{
    position:absolute;left:100px;top:200px;width:1000px;height:568px;
    border-radius:30px;overflow:hidden;
    background:linear-gradient(160deg,var(--card-frost) 0%,var(--card-frost-deep) 100%);
    box-shadow:0 18px 40px rgba(0,0,0,.18);
  }
  .card__shade{position:absolute;inset:0;width:100%;height:100%}
  .card__emblem-area{
    position:absolute;left:170px;top:0;width:500px;height:568px;
    background:radial-gradient(ellipse 60% 55% at 55% 50%,rgba(31,120,193,.85) 0%,rgba(15,79,140,.55) 45%,rgba(15,79,140,0) 75%);
  }
  .brand{position:absolute;left:55px;top:92px;color:var(--brand-blue)}
  .brand__name{font:700 72px/1 "Nunito",sans-serif;letter-spacing:1px}
  .brand__tagline{font:400 19px/1 "Nunito",sans-serif;margin-top:14px;letter-spacing:.3px}
  .contact{position:absolute;right:36px;top:240px;text-align:right;color:var(--ink);
    font:400 22px/31px "Roboto",sans-serif}
  .contact__row{display:flex;justify-content:flex-end;align-items:center;gap:12px;height:31px}
  .contact__icon{width:20px;height:20px;fill:var(--brand-blue)}
  .contact__address{margin-top:10px;margin-right:32px}
  .person{position:absolute;right:68px;top:452px;color:var(--brand-blue);
    font:700 30px/1 "Roboto",sans-serif;white-space:nowrap}
  .person__creds{font-size:19px;font-weight:700}
  .motto{position:absolute;right:36px;top:512px;font:400 22px/1 "Roboto",sans-serif;color:var(--ink)}
</style>
</head>
<body>
  <div class="card">
    <svg class="card__shade" viewBox="0 0 1000 568" preserveAspectRatio="none" aria-hidden="true">
      <defs>
        <linearGradient id="darkFill" x1="0" y1="0" x2="1" y2="1">
          <stop offset="0" stop-color="#2a2c30"/>
          <stop offset=".5" stop-color="#0b0c0e"/>
          <stop offset="1" stop-color="#16171a"/>
        </linearGradient>
      </defs>
      <path d="M0 0 H680 C640 160 560 300 420 380 C320 440 230 500 170 568 H0 Z" fill="url(#darkFill)"/>
    </svg>

    <div class="card__emblem-area" role="img" aria-label="Large blue winged emblem decoration sweeping across the card"></div>

    <div class="brand">
      <div class="brand__name">VALMIRA</div>
      <div class="brand__tagline">Integrative Holistic Medicine</div>
    </div>

    <div class="contact">
      <div class="contact__row">512 555 0148
        <svg class="contact__icon" viewBox="0 0 24 24"><path d="M6.6 10.8a15 15 0 0 0 6.6 6.6l2.2-2.2a1 1 0 0 1 1-.25 11.4 11.4 0 0 0 3.6.57 1 1 0 0 1 1 1V20a1 1 0 0 1-1 1A17 17 0 0 1 3 4a1 1 0 0 1 1-1h3.5a1 1 0 0 1 1 1c0 1.25.2 2.45.57 3.57a1 1 0 0 1-.25 1z"/></svg>
      </div>
      <div class="contact__row">818 555 0192
        <svg class="contact__icon" viewBox="0 0 24 24"><path d="M7 1h10a2 2 0 0 1 2 2v18a2 2 0 0 1-2 2H7a2 2 0 0 1-2-2V3a2 2 0 0 1 2-2zm0 3v14h10V4zm5 15.5a1 1 0 1 0 0 2 1 1 0 0 0 0-2z"/></svg>
      </div>
      <div class="contact__row">t.wrenfeld@ValmiraHealth.example
        <svg class="contact__icon" viewBox="0 0 24 24"><path d="M2 5h20v14H2zm2 2v.5l8 5 8-5V7zm0 2.8V17h16V9.8l-8 5z"/></svg>
      </div>
      <div class="contact__row">www.ValmiraHealth.example
        <svg class="contact__icon" viewBox="0 0 24 24"><path d="M12 2a10 10 0 1 0 0 20 10 10 0 0 0 0-20zm6.9 6h-3a15 15 0 0 0-1.3-3.9A8 8 0 0 1 18.9 8zM12 4c.9 1.2 1.6 2.6 2 4h-4c.4-1.4 1.1-2.8 2-4zM4.3 14a8 8 0 0 1 0-4h3.4a16 16 0 0 0 0 4zm.8 2h3a15 15 0 0 0 1.3 3.9A8 8 0 0 1 5.1 16zm3-8h-3a8 8 0 0 1 4.3-3.9A15 15 0 0 0 8.1 8zM12 20c-.9-1.2-1.6-2.6-2-4h4c-.4 1.4-1.1 2.8-2 4zm2.3-6H9.7a14 14 0 0 1 0-4h4.6a14 14 0 0 1 0 4zm.3 5.9a15 15 0 0 0 1.3-3.9h3a8 8 0 0 1-4.3 3.9zm1.7-5.9a16 16 0 0 0 0-4h3.4a8 8 0 0 1 0 4z"/></svg>
      </div>
      <div class="contact__address">4100 East Marrow Drive<br>Austin, TX 78119</div>
    </div>

    <div class="person">TOBIAS WRENFELD <span class="person__creds">- DOE, CPT, LMT</span></div>

    <div class="motto">it’s all about you – your health, your objectives</div>
  </div>
</body>
</html>
```